Coffee House With Cycling Theme Wants Business Cards

We want to create a business card for a coffee house that has a cycling theme. We expect to use the current logo on one side of the business card and we have been considering adding the words 'COFFEE HOUSE' underneath (see example). For the other side of the business card we want an interesting design with tag-line, address and social media links (the normal business card stuff). See examples provided but we are not fixed on having it exactly as shown, we are very open to great creative ideas. Please note our logo has the initials ‘KR' in orange embedded in the design and this must be retained. However, you can play with the words COFFEE HOUSE as well as use the orange color on the backside of the business card, as you see fit. For an image on the backside of the business card it can be a photo, hand-drawn or whatever but it must visually combine coffee and cycling in some way. The interior of the Coffee House will be reclaimed wood, rustic and have an urban feel to it with cycling artifacts hanging from the walls/ceiling, etc. Finally, it would be beneficial if the business card design elements can be easily used on flyers and other promotional assets. Good luck, we are looking forward to seeing your creative ideas.

Target Market(s)

Coffee lovers and cycling fans

Contact Information for Business Card

See project description.

Colors

Designer to choose colors to be used in the design.

Requirements
Must have
• Must use the current logo provided and combine a coffee and bike theme.
Nice to have
• Orange is used in current logo and could be used as an accent color on the backside of the business card.

```html
<!DOCTYPE html>
<html lang="en">
<head>
<meta charset="utf-8">
<title>KR Coffee House – Business Card</title>
<link rel="stylesheet" href="https://fonts.googleapis.com/css2?family=Work+Sans:wght@400;500;600&display=swap">
<style>
  :root {
    --orange: #e5612a;
    --orange-deep: #c44f1e;
    --charcoal: #3a3a3a;
    --ink: #1c1c1c;
    --text: #333333;
    --paper: #ffffff;
    --stage: #e9e9e9;
    --logo-light: #d9d9d9;
  }
  * { box-sizing: border-box; margin: 0; padding: 0; }
  html, body { width: 1200px; height: 900px; overflow: hidden; }
  body {
    background: var(--stage);
    font-family: "Work Sans", Arial, sans-serif;
    position: relative;
  }
  .card {
    position: absolute;
    left: 250px;
    width: 700px;
    height: 400px;
    border-radius: 20px;
    overflow: hidden;
    box-shadow: 0 6px 18px rgba(0,0,0,0.18);
  }
  .card--front { top: 40px; background: var(--paper); }
  .card--back {
    top: 470px;
    background: linear-gradient(135deg, var(--orange) 0%, var(--orange-deep) 100%);
  }
  .swoosh { position: absolute; inset: 0; width: 100%; height: 100%; }
  .contact {
    position: absolute;
    left: 44px;
    top: 48px;
    color: var(--text);
    font-size: 15px;
    line-height: 1.55;
  }
  .contact__name {
    color: var(--orange);
    font-weight: 500;
    font-size: 24px;
    letter-spacing: 1px;
    text-transform: uppercase;
  }
  .contact__role { font-size: 15px; margin-bottom: 10px; }
  .contact__address { margin-bottom: 8px; }
  .contact__row { display: flex; align-items: center; gap: 9px; }
  .contact__row svg { width: 14px; height: 14px; flex: none; }
  .contact__social-mark {
    width: 18px; height: 18px; border-radius: 3px; flex: none;
    background: var(--charcoal);
  }
  .contact__social { margin-top: 4px; gap: 8px; }
  .brand {
    position: absolute;
    display: flex;
    align-items: center;
    gap: 14px;
    font-weight: 500;
    letter-spacing: 2px;
    white-space: nowrap;
  }
  .brand__dot { border-radius: 50%; flex: none; }
  .brand--front { right: 46px; bottom: 44px; font-size: 38px; color: var(--ink); }
  .brand--front .brand__dot { width: 22px; height: 22px; background: var(--orange); }
  .brand--back {
    left: 50%; top: 50%; transform: translate(-50%, -50%);
    font-size: 48px; color: var(--logo-light);
  }
  .brand--back .brand__dot { width: 26px; height: 26px; background: var(--logo-light); }
</style>
</head>
<body>
  <section class="card card--front">
    <svg class="swoosh" viewBox="0 0 700 400" aria-hidden="true">
      <path d="M300,0 C440,20 500,170 580,270 C620,320 660,335 700,340 L700,0 Z" fill="var(--orange)"/>
      <path d="M300,0 C440,20 500,170 580,270 C620,320 660,335 700,340" fill="none" stroke="var(--charcoal)" stroke-width="9"/>
      <path d="M250,0 C370,18 420,90 450,140" fill="none" stroke="var(--orange)" stroke-width="5"/>
      <path d="M255,14 C360,30 400,70 420,100" fill="none" stroke="var(--charcoal)" stroke-width="3"/>
    </svg>

    <div class="contact">
      <p class="contact__name">Daniel Hart</p>
      <p class="contact__role">Director</p>
      <p class="contact__address">128 Ferrow Lane,<br>Lindmoor, NZ, 8120</p>
      <p class="contact__row">
        <svg viewBox="0 0 24 24"><path d="M6.6 10.8a15 15 0 0 0 6.6 6.6l2.2-2.2a1 1 0 0 1 1-.25 11 11 0 0 0 3.6.6 1 1 0 0 1 1 1V20a1 1 0 0 1-1 1A17 17 0 0 1 3 4a1 1 0 0 1 1-1h3.5a1 1 0 0 1 1 1 11 11 0 0 0 .6 3.6 1 1 0 0 1-.25 1z" fill="var(--orange)"/></svg>
        (555) 210-4478
      </p>
      <p class="contact__row">
        <svg viewBox="0 0 24 24"><rect x="3" y="5" width="18" height="14" rx="2" fill="none" stroke="var(--orange)" stroke-width="2"/><path d="M3 7l9 6 9-6" fill="none" stroke="var(--orange)" stroke-width="2"/></svg>
        info@krcoffeehouse.com
      </p>
      <p class="contact__row">
        <svg viewBox="0 0 24 24"><circle cx="12" cy="12" r="9" fill="none" stroke="var(--orange)" stroke-width="2"/><path d="M3 12h18M12 3c3 3 3 15 0 18M12 3c-3 3-3 15 0 18" fill="none" stroke="var(--orange)" stroke-width="1.5"/></svg>
        www.krcoffeehouse.com
      </p>
      <p class="contact__row contact__social"><span class="contact__social-mark"></span>krcoffeehouse.com</p>
      <p class="contact__row contact__social"><span class="contact__social-mark"></span>krcoffeehouse.com</p>
    </div>

    <div class="brand brand--front"><span class="brand__dot"></span>KR COFFEE HOUSE</div>
  </section>

  <section class="card card--back">
    <div class="brand brand--back"><span class="brand__dot"></span>KR COFFEE HOUSE</div>
  </section>
</body>
</html>
```